Pharmacy ad

need 2 pharmacy ads for the phone book. one for Brookvale Pharmacy and one for Cedarline Care Pharmacy. Dimensions for ad is 4.75in x 4.667 in. please see attached examples of ad uploaded as well logos of each pharmacy

```html
<!DOCTYPE html>
<html lang="en">
<head>
<meta charset="utf-8">
<title>Pharmacy Directory Ads</title>
<link rel="stylesheet" href="https://fonts.googleapis.com/css2?family=Montserrat:wght@300;400;600;700;800&family=Quicksand:wght@500;600;700&family=Kaushan+Script&display=swap">
<style>
:root{
  --page:#fdf1a4;
  --navy:#1d1f4a;
  --sky:#bfe3f4;
  --sky-deep:#6bbde0;
  --leaf:#8cc63f;
  --leaf-soft:#c9e39a;
  --leaf-pale:#dcedb8;
  --royal:#3a4fa8;
  --fb:#3b5aa0;
  --white:#ffffff;
  --badge:#e4e7ee;
}
*{margin:0;padding:0;box-sizing:border-box}
html,body{width:1200px;height:600px;overflow:hidden;background:var(--page)}
body{position:relative;font-family:"Montserrat",sans-serif;color:var(--navy)}
.ad{position:absolute;top:22px;height:556px;overflow:hidden}
.ad-brookvale{left:20px;width:566px;border:1px solid var(--navy)}
.ad-cedarline{left:611px;width:570px;border:2px solid var(--leaf)}
.ad-bg{position:absolute;inset:0}
.abs{position:absolute}
.bold{font-weight:700}

/* Brookvale */
.offer{position:absolute;left:10px;width:244px;text-align:center;line-height:1}
.offer .pct{font-size:40px;font-weight:800;letter-spacing:-1px}
.offer .light{font-size:19px;font-weight:400;line-height:1.05}
.offer .strong{font-size:19px;font-weight:700;line-height:1.1}
.dots{position:absolute;border-top:3px dotted var(--navy)}
.brand-name{position:absolute;left:300px;width:256px;text-align:center;font-weight:800;font-size:36px;line-height:1.05;color:var(--navy)}
.tagline{position:absolute;left:300px;width:256px;text-align:center;font-style:italic;font-size:13px;color:#4e9a3a}
.services{position:absolute;list-style:none;font-size:12px;font-weight:700;line-height:1.15}
.services li{position:relative;padding-left:10px;margin-bottom:8px}
.services li::before{content:"";position:absolute;left:0;top:4px;width:5px;height:5px;background:var(--navy);transform:rotate(45deg)}
.contact{position:absolute;font-size:12px;font-weight:600;line-height:1.2}
.contact small{display:block;font-size:10px;font-weight:400;padding-left:16px}
.icon{display:inline-block;vertical-align:-2px;margin-right:4px}
.hours{position:absolute;font-size:13px;font-weight:700;line-height:1.35}
.divider{position:absolute;width:1.5px;background:var(--navy)}
.visit{position:absolute;width:90px;text-align:center;font-size:13px}
.social{position:absolute;width:46px;height:46px;border-radius:50%;background:var(--fb)}
.badge{position:absolute;border-radius:3px;background:var(--badge);border:1px solid #c9ced8}

/* Cedarline */
.photo{position:absolute;left:0;top:0;width:570px;height:210px;background:linear-gradient(90deg,#e9ecef 0%,#f2f3f4 45%,#d8cfc8 70%,#b89a86 100%)}
.cl-name{position:absolute;left:82px;top:62px;font-family:"Quicksand",sans-serif;font-weight:700;color:var(--royal);line-height:1}
.cl-name .main{display:block;font-size:34px}
.cl-name .sub{display:block;font-size:16px;letter-spacing:1px;margin-top:4px;padding-left:58px}
.cl-mark{position:absolute;left:40px;top:68px;width:30px;height:30px;background:var(--leaf)}
.accept{position:absolute;left:78px;top:128px;font-size:12px;font-weight:700}
.slogan{position:absolute;left:0;width:570px;top:212px;text-align:center;font-family:"Kaushan Script",cursive;font-size:47px;color:var(--royal)}
.cl-offer{position:absolute;left:28px;color:var(--royal);display:flex;align-items:center;gap:8px}
.cl-offer .pct{font-size:54px;font-weight:800;letter-spacing:-2px;line-height:1}
.cl-offer .txt{font-size:15px;font-weight:400;line-height:1}
.cl-offer .txt b{display:block;font-size:25px;font-weight:400}
.cl-offer .txt small{display:block;font-size:10px;font-weight:600}
.cl-rule{position:absolute;left:276px;top:318px;width:3px;height:124px;background:var(--leaf)}
.cl-services{position:absolute;list-style:none;font-family:"Quicksand",sans-serif;font-weight:600;font-size:13px;color:var(--royal);line-height:1.1}
.cl-services li{position:relative;padding-left:10px;margin-bottom:8px}
.cl-services li::before{content:"";position:absolute;left:0;top:5px;width:5px;height:5px;border-radius:50%;background:var(--royal)}
.cl-contact{position:absolute;font-size:12.5px;font-weight:700;color:var(--navy)}
.cl-hours{position:absolute;left:30px;top:518px;font-size:16px;font-weight:700}
</style>
</head>
<body>

<!-- Brookvale Pharmacy -->
<section class="ad ad-brookvale">
  <svg class="ad-bg" width="566" height="556" viewBox="0 0 566 556">
    <defs>
      <linearGradient id="skyFade" x1="0" y1="0" x2="1" y2="0">
        <stop offset="0" stop-color="#9fd4ee"/><stop offset="1" stop-color="#e3f3fb"/>
      </linearGradient>
      <linearGradient id="leafFade" x1="0" y1="0" x2="0" y2="1">
        <stop offset="0" stop-color="#9fd05a"/><stop offset="1" stop-color="#d4eba8"/>
      </linearGradient>
    </defs>
    <rect width="566" height="556" fill="url(#skyFade)"/>
    <rect y="258" width="566" height="298" fill="url(#leafFade)"/>
    <path d="M306,0 L566,0 L566,404 C430,430 290,340 290,200 C290,110 298,50 306,0 Z" fill="var(--sky-deep)"/>
    <path d="M320,0 L566,0 L566,390 C440,412 306,330 306,200 C306,110 312,50 320,0 Z" fill="#f4f9fc"/>
  </svg>

  <div class="offer" style="top:22px">
    <div class="pct">10%</div>
    <div class="light">SENIOR CITIZEN<br>DISCOUNT</div>
    <div class="strong">FOR PATIENTS 60<br>YEARS AND OVER</div>
  </div>
  <div class="dots" style="left:62px;top:152px;width:138px"></div>
  <div class="offer" style="top:168px">
    <div class="pct">10%</div>
    <div class="light">STUDENT DISCOUNT</div>
    <div class="strong">WITH VALID ID CARD</div>
  </div>

  <svg class="abs" style="left:398px;top:64px" width="60" height="60" viewBox="0 0 60 60"><circle cx="30" cy="30" r="28" fill="var(--leaf)"/></svg>
  <div class="brand-name" style="top:172px">BROOKVALE<br>PHARMACY</div>
  <div class="tagline" style="top:254px">We Care About Your Health</div>

  <div class="badge" style="left:368px;top:308px;width:50px;height:32px"></div>
  <div class="badge" style="left:432px;top:308px;width:50px;height:32px"></div>
  <div class="badge" style="left:496px;top:308px;width:44px;height:32px"></div>
  <div class="badge" style="left:398px;top:348px;width:116px;height:26px"></div>

  <ul class="services" style="left:28px;top:280px;width:150px">
    <li>Certified Pharmacists</li>
    <li>Affordable prices</li>
    <li>Brand and Generic Medicines</li>
    <li>Blood Pressure and Glucose checks</li>
  </ul>
  <ul class="services" style="left:172px;top:280px;width:130px">
    <li>Personal care and Beauty Products</li>
    <li>Injectables</li>
    <li>Special Orders</li>
    <li>Delivery service</li>
  </ul>

  <div class="dots" style="left:28px;top:402px;width:372px"></div>
  <div class="contact" style="left:28px;top:420px;font-size:13px;font-weight:400">For more inquiries, email us: brookvalerx@mailbox.kn</div>

  <div class="contact" style="left:28px;top:444px">
    <svg class="icon" width="10" height="13" viewBox="0 0 10 13"><path d="M5 0C2.2 0 0 2.2 0 5c0 3.5 5 8 5 8s5-4.5 5-8C10 2.2 7.8 0 5 0zm0 7a2 2 0 110-4 2 2 0 010 4z" fill="var(--navy)"/></svg>27 Harbour Lane, Porttown
    <small>(opposite Grace Chapel)</small>
    <div style="margin-top:3px"><svg class="icon" width="13" height="11" viewBox="0 0 13 11"><path d="M1 3C1 1 3 0 6.5 0S12 1 12 3v1H9V3H4v1H1zM2 5h9l1 6H1z" fill="var(--navy)"/></svg>1 555 410 2074</div>
  </div>
  <div class="divider" style="left:262px;top:444px;height:110px"></div>
  <div class="contact" style="left:272px;top:444px">
    <svg class="icon" width="10" height="13" viewBox="0 0 10 13"><path d="M5 0C2.2 0 0 2.2 0 5c0 3.5 5 8 5 8s5-4.5 5-8C10 2.2 7.8 0 5 0zm0 7a2 2 0 110-4 2 2 0 010 4z" fill="var(--navy)"/></svg>Marina Walk, Food Court,
    <small style="font-size:12px;font-weight:600;margin-top:-1px">Porttown</small>
    <div style="margin-top:3px"><svg class="icon" width="13" height="11" viewBox="0 0 13 11"><path d="M1 3C1 1 3 0 6.5 0S12 1 12 3v1H9V3H4v1H1zM2 5h9l1 6H1z" fill="var(--navy)"/></svg>1 555 410 2077</div>
  </div>

  <div class="hours" style="left:28px;top:500px">MONDAY – FRIDAY 10AM TO 6PM<br>SATURDAY 10AM TO 5PM</div>
  <div class="hours" style="left:272px;top:500px">MONDAY – SATURDAY<br>9AM TO 5PM</div>

  <div class="visit" style="left:459px;top:462px">Visit us on</div>
  <div class="social" style="left:481px;top:487px"></div>
</section>

<!-- Cedarline Care Pharmacy -->
<section class="ad ad-cedarline">
  <div class="photo" role="img" aria-label="Photo of a smiling pharmacist in glasses and a white coat reaching for medicine on a shelf"></div>
  <svg class="ad-bg" width="570" height="556" viewBox="0 0 570 556">
    <path d="M0,166 C140,176 300,196 420,186 C490,180 540,168 570,160 L570,570 L0,570 Z" fill="var(--royal)"/>
    <path d="M0,174 C140,184 300,204 420,194 C490,188 540,176 570,168 L570,570 L0,570 Z" fill="var(--leaf-soft)"/>
    <path d="M0,196 C160,206 320,222 440,212 C500,206 545,196 570,190 L570,570 L0,570 Z" fill="var(--leaf)" opacity="0.55"/>
    <path d="M0,300 C150,286 320,286 440,296 C500,302 545,308 570,312 L570,570 L0,570 Z" fill="var(--royal)"/>
    <path d="M0,306 C150,292 320,292 440,302 C500,308 545,314 570,318 L570,570 L0,570 Z" fill="var(--white)"/>
    <rect y="446" width="570" height="110" fill="var(--leaf)"/>
  </svg>

  <div class="cl-mark"></div>
  <div class="cl-name"><span class="main">Cedarline Care</span><span class="sub">PHARMACY</span></div>

  <div class="accept">WE ACCEPT:</div>
  <div class="badge" style="left:78px;top:146px;width:42px;height:26px"></div>
  <div class="badge" style="left:132px;top:146px;width:42px;height:26px"></div>
  <div class="badge" style="left:186px;top:146px;width:34px;height:28px"></div>
  <div class="badge" style="left:230px;top:148px;width:110px;height:24px"></div>

  <div class="slogan">Where good health begins</div>

  <div class="cl-offer" style="top:316px"><span class="pct">10%</span><span class="txt">SENIOR CITIZEN<b>DISCOUNT</b></span></div>
  <div class="cl-offer" style="top:374px"><span class="pct">10%</span><span class="txt">STUDENT<b>DISCOUNT</b><small>(WITH VALID ID CARD)</small></span></div>

  <div class="cl-rule"></div>
  <ul class="cl-services" style="left:290px;top:322px;width:134px">
    <li>Certified Pharmacists</li>
    <li>Affordable prices</li>
    <li>Brand and Generic Medicines</li>
    <li>Blood Pressure and Glucose checks</li>
  </ul>
  <ul class="cl-services" style="left:426px;top:322px;width:124px">
    <li>Personal care and Beauty Products</li>
    <li>Injectables</li>
    <li>Special Orders</li>
    <li>Delivery service</li>
  </ul>

  <div class="cl-contact" style="left:30px;top:466px">
    <svg class="icon" width="10" height="13" viewBox="0 0 10 13"><path d="M5 0C2.2 0 0 2.2 0 5c0 3.5 5 8 5 8s5-4.5 5-8C10 2.2 7.8 0 5 0zm0 7a2 2 0 110-4 2 2 0 010 4z" fill="var(--royal)"/></svg>Unit C1, Seabreeze Hotel, Shore Road, Porttown
  </div>
  <div class="cl-contact" style="left:30px;top:490px">
    <svg class="icon" width="14" height="10" viewBox="0 0 14 10"><rect width="14" height="10" rx="1" fill="var(--royal)"/><path d="M1 1l6 5 6-5" fill="none" stroke="var(--white)" stroke-width="1.2"/></svg>cedarline555@mailbox.kn
  </div>
  <div class="cl-contact" style="left:225px;top:490px">
    <svg class="icon" width="15" height="12" viewBox="0 0 13 11"><path d="M1 3C1 1 3 0 6.5 0S12 1 12 3v1H9V3H4v1H1zM2 5h9l1 6H1z" fill="var(--royal)"/></svg>&nbsp;1 555 465 3072
  </div>
  <div class="cl-hours">MONDAY – SATURDAY 8AM TO 7PM</div>

  <div class="visit" style="left:461px;top:466px">Visit us on</div>
  <div class="social" style="left:483px;top:485px"></div>
</section>

</body>
</html>
```